Velmora Consulting Business

** Please add the content information from my old business card
1. I would like to see a two sided business card with both options with the 1st Option--Tallow Spire-new WHITE BACKGROUND LOGO
2 nd Option-Tallow Spire - new BLACK- Background Logo
3rd -Option a business card with my Photo on the card
Please add the new word to the card information:
EXECUTION
AS THE OWNER'S REP
WE AIM TO ACHIEVE YOUR
INFRASTRUCTURE VISION with
OUR SPECIALIZATION & EXECUTION in:

FUNDING Planning
BUSINESS Planning
INFRASTRUCTURE Planning
PROJECT Management
Since 2012
_____________________________________________________________________
I want to get spot uv raised printing. I was liking a a nice rich white linen paper stock with black writing & NOT A COLORED CARD other than a variety of white or black cards concept

```html
<!DOCTYPE html>
<html lang="en">
<head>
<meta charset="utf-8">
<title>Velmora Consulting – Business Card Options</title>
<link href="https://fonts.googleapis.com/css2?family=Montserrat:wght@400;500;700;800&display=swap" rel="stylesheet">
<style>
  :root{
    --stage:#2b2b2b;
    --black:#050505;
    --red:#e8173a;
    --white:#ffffff;
    --paper:#fbfaf6;
    --photo-a:#6b6f76;
    --photo-b:#3b3e44;
  }
  *{box-sizing:border-box;margin:0;padding:0}
  html,body{width:1200px;height:689px;overflow:hidden}
  body{
    background:var(--stage);
    font-family:"Montserrat",Arial,sans-serif;
    display:grid;
    grid-template-columns:repeat(3,372px);
    grid-template-rows:repeat(2,213px);
    column-gap:24px;row-gap:30px;
    justify-content:center;align-content:center;
  }

  .card{
    --ink:var(--white);
    --bg:var(--black);
    --band-end:var(--white);
    position:relative;width:372px;height:213px;
    background:var(--bg);color:var(--ink);
    border-radius:14px;overflow:hidden;
    box-shadow:0 14px 30px rgba(0,0,0,.5);
  }
  .card--white{--ink:var(--black);--bg:var(--paper);--band-end:var(--black)}

  /* wordmark */
  .wordmark{position:absolute;display:flex;align-items:center;gap:8px}
  .wordmark__mark{width:10px;height:10px;background:var(--ink)}
  .wordmark__name{color:var(--ink);font-weight:700;line-height:1.05}

  /* back side */
  .back .wordmark{left:22px;top:86px}
  .back .wordmark__name{font-size:17px}
  .divider{position:absolute;left:172px;top:28px;width:1.5px;height:152px;background:var(--red)}
  .pitch{position:absolute;left:184px;top:32px;width:176px}
  .pitch__lead{
    color:var(--red);font-weight:800;font-size:7.6px;line-height:1.4;
    text-transform:uppercase;letter-spacing:.2px;margin-bottom:10px
  }
  .pitch__lead span{text-transform:none}
  .services{list-style:none}
  .services li{
    font-size:9px;font-weight:500;line-height:1.75;
    display:flex;align-items:center;gap:6px
  }
  .services li::before{content:"";width:4px;height:4px;border-radius:50%;background:var(--red);flex:none}
  .since{position:absolute;right:20px;bottom:16px;font-size:8.5px;font-weight:500}

  /* front side */
  .front .wordmark{left:20px;top:20px}
  .front .wordmark__name{font-size:15px}
  .person{position:absolute;left:20px;top:70px}
  .person__name{color:var(--red);font-weight:700;font-size:17px}
  .person__title{font-size:8.8px;font-weight:500;margin-top:3px;text-transform:uppercase;letter-spacing:.2px}
  .rule{position:absolute;left:20px;right:20px;top:117px;height:1px;background:var(--red)}
  .contacts{position:absolute;left:20px;top:126px;list-style:none}
  .contacts li{display:flex;align-items:center;gap:7px;font-size:9px;line-height:1.75}
  .contacts svg{width:9px;height:9px;fill:var(--red);flex:none}
  .locations{position:absolute;right:20px;top:166px;font-size:8.8px;font-weight:500}
  .base-band{position:absolute;left:0;bottom:0;width:372px;height:14px}
  .base-band .band-end{fill:var(--band-end)}

  /* photo option */
  .card--photo .person__name{font-size:16px}
  .card--photo .rule{right:20px}
  .portrait{
    position:absolute;right:20px;top:20px;width:84px;height:88px;border-radius:8px;
    background:linear-gradient(160deg,var(--photo-a),var(--photo-b));
    border:1.5px solid var(--red);
  }
</style>
</head>
<body>

  <!-- Row 1: backs -->
  <section class="card card--white back" aria-label="Option 1, white card back">
    <div class="wordmark"><span class="wordmark__mark"></span><span class="wordmark__name">Velmora<br>Consulting</span></div>
    <div class="divider"></div>
    <div class="pitch">
      <p class="pitch__lead">As the owner's rep<br>we aim to achieve your<br>infrastructure vision <span>with</span><br>our specialization &amp;<br>execution <span>in:</span></p>
      <ul class="services">
        <li>FUNDING Planning</li><li>BUSINESS Planning</li><li>INFRASTRUCTURE Planning</li><li>PROJECT Management</li>
      </ul>
    </div>
    <p class="since">Since 2012</p>
  </section>

  <section class="card back" aria-label="Option 2, black card back">
    <div class="wordmark"><span class="wordmark__mark"></span><span class="wordmark__name">Velmora<br>Consulting</span></div>
    <div class="divider"></div>
    <div class="pitch">
      <p class="pitch__lead">As the owner's rep<br>we aim to achieve your<br>infrastructure vision <span>with</span><br>our specialization &amp;<br>execution <span>in:</span></p>
      <ul class="services">
        <li>FUNDING Planning</li><li>BUSINESS Planning</li><li>INFRASTRUCTURE Planning</li><li>PROJECT Management</li>
      </ul>
    </div>
    <p class="since">Since 2012</p>
  </section>

  <section class="card back" aria-label="Option 3, photo card back">
    <div class="wordmark"><span class="wordmark__mark"></span><span class="wordmark__name">Velmora<br>Consulting</span></div>
    <div class="divider"></div>
    <div class="pitch">
      <p class="pitch__lead">As the owner's rep<br>we aim to achieve your<br>infrastructure vision <span>with</span><br>our specialization &amp;<br>execution <span>in:</span></p>
      <ul class="services">
        <li>FUNDING Planning</li><li>BUSINESS Planning</li><li>INFRASTRUCTURE Planning</li><li>PROJECT Management</li>
      </ul>
    </div>
    <p class="since">Since 2012</p>
  </section>

  <!-- Row 2: fronts -->
  <section class="card card--white front" aria-label="Option 1, white card front">
    <div class="wordmark"><span class="wordmark__mark"></span><span class="wordmark__name">Velmora<br>Consulting</span></div>
    <div class="person"><p class="person__name">Renata Halvorsen-Quill</p><p class="person__title">CEO / Lead Project Manager</p></div>
    <div class="rule"></div>
    <ul class="contacts">
      <li><svg viewBox="0 0 24 24" aria-hidden="true"><path d="M6.6 10.8a15.1 15.1 0 006.6 6.6l2.2-2.2a1 1 0 011-.25 11.4 11.4 0 003.6.57 1 1 0 011 1V20a1 1 0 01-1 1A17 17 0 013 4a1 1 0 011-1h3.5a1 1 0 011 1 11.4 11.4 0 00.57 3.6 1 1 0 01-.25 1z"/></svg>555.014.2290</li>
      <li><svg viewBox="0 0 24 24" aria-hidden="true"><path d="M2 5h20v14H2zm2 2v.5l8 5 8-5V7l-8 5z"/></svg>renata@velmora.ca</li>
      <li><svg viewBox="0 0 24 24" aria-hidden="true"><circle cx="12" cy="12" r="9" fill="none" stroke="#e8173a" stroke-width="2"/><path d="M3 12h18M12 3c3 3 3 15 0 18M12 3c-3 3-3 15 0 18" fill="none" stroke="#e8173a" stroke-width="1.6"/></svg>www.velmora.ca</li>
    </ul>
    <p class="locations">Northvale NT · Harrowby NB</p>
    <svg class="base-band" viewBox="0 0 372 14" preserveAspectRatio="none" aria-hidden="true">
      <polygon points="0,5 234,5 228,14 0,14" fill="#e8173a"/>
      <polygon class="band-end" points="238,0 372,0 372,14 231,14"/>
    </svg>
  </section>

  <section class="card front" aria-label="Option 2, black card front">
    <div class="wordmark"><span class="wordmark__mark"></span><span class="wordmark__name">Velmora<br>Consulting</span></div>
    <div class="person"><p class="person__name">Renata Halvorsen-Quill</p><p class="person__title">CEO / Lead Project Manager</p></div>
    <div class="rule"></div>
    <ul class="contacts">
      <li><svg viewBox="0 0 24 24" aria-hidden="true"><path d="M6.6 10.8a15.1 15.1 0 006.6 6.6l2.2-2.2a1 1 0 011-.25 11.4 11.4 0 003.6.57 1 1 0 011 1V20a1 1 0 01-1 1A17 17 0 013 4a1 1 0 011-1h3.5a1 1 0 011 1 11.4 11.4 0 00.57 3.6 1 1 0 01-.25 1z"/></svg>555.014.2290</li>
      <li><svg viewBox="0 0 24 24" aria-hidden="true"><path d="M2 5h20v14H2zm2 2v.5l8 5 8-5V7l-8 5z"/></svg>renata@velmora.ca</li>
      <li><svg viewBox="0 0 24 24" aria-hidden="true"><circle cx="12" cy="12" r="9" fill="none" stroke="#e8173a" stroke-width="2"/><path d="M3 12h18M12 3c3 3 3 15 0 18M12 3c-3 3-3 15 0 18" fill="none" stroke="#e8173a" stroke-width="1.6"/></svg>www.velmora.ca</li>
    </ul>
    <p class="locations">Northvale NT · Harrowby NB</p>
    <svg class="base-band" viewBox="0 0 372 14" preserveAspectRatio="none" aria-hidden="true">
      <polygon points="0,5 234,5 228,14 0,14" fill="#e8173a"/>
      <polygon class="band-end" points="238,0 372,0 372,14 231,14"/>
    </svg>
  </section>

  <section class="card card--photo front" aria-label="Option 3, photo card front">
    <div class="wordmark"><span class="wordmark__mark"></span><span class="wordmark__name">Velmora<br>Consulting</span></div>
    <div class="portrait" role="img" aria-label="Portrait photo of the card holder"></div>
    <div class="person"><p class="person__name">Renata Halvorsen-Quill</p><p class="person__title">CEO / Lead Project Manager</p></div>
    <div class="rule"></div>
    <ul class="contacts">
      <li><svg viewBox="0 0 24 24" aria-hidden="true"><path d="M6.6 10.8a15.1 15.1 0 006.6 6.6l2.2-2.2a1 1 0 011-.25 11.4 11.4 0 003.6.57 1 1 0 011 1V20a1 1 0 01-1 1A17 17 0 013 4a1 1 0 011-1h3.5a1 1 0 011 1 11.4 11.4 0 00.57 3.6 1 1 0 01-.25 1z"/></svg>555.014.2290</li>
      <li><svg viewBox="0 0 24 24" aria-hidden="true"><path d="M2 5h20v14H2zm2 2v.5l8 5 8-5V7l-8 5z"/></svg>renata@velmora.ca</li>
      <li><svg viewBox="0 0 24 24" aria-hidden="true"><circle cx="12" cy="12" r="9" fill="none" stroke="#e8173a" stroke-width="2"/><path d="M3 12h18M12 3c3 3 3 15 0 18M12 3c-3 3-3 15 0 18" fill="none" stroke="#e8173a" stroke-width="1.6"/></svg>www.velmora.ca</li>
    </ul>
    <p class="locations">Northvale NT · Harrowby NB</p>
    <svg class="base-band" viewBox="0 0 372 14" preserveAspectRatio="none" aria-hidden="true">
      <polygon points="0,5 234,5 228,14 0,14" fill="#e8173a"/>
      <polygon class="band-end" points="238,0 372,0 372,14 231,14"/>
    </svg>
  </section>

</body>
</html>
```